Dental specialist needs a sharp looking letterhead

I am looking for a letterhead to be used to send letters and communication between myself (a dental specialist) and other dentists.
My office is a state of the art dental specialty office.
I need to letterhead to also state:
Bertram L. Oswick DDS
2748 Tollard Avenue, Suite K
West Tollard, NY 14391
(716)392-5061
fax: (716)392-5087
oswickroot.com (**this email address may change)

i included my logo designs.
thank you

Target Market(s)

dentists

Industry/Entity Type

Communication

Requirements
Must have
• the included logo, whether the vertical or horizontal versions

```html
<!DOCTYPE html>
<html lang="en">
<head>
<meta charset="utf-8">
<title>Keystone Endodontics P.C. Letterhead</title>
<link rel="stylesheet" href="https://fonts.googleapis.com/css2?family=Domine:wght@500&family=Roboto+Slab:wght@300;400&display=swap">
<style>
  :root {
    --paper: #ffffff;
    --ink: #1a1a1a;
    --ink-soft: #3a3a3a;
    --brand-blue: #4aa3df;
    --brand-green: #8cc63f;
    --rule: #333333;
  }
  * { margin: 0; padding: 0; box-sizing: border-box; }
  html, body { width: 931px; height: 1200px; overflow: hidden; background: var(--paper); }
  .letterhead { position: relative; width: 931px; height: 1200px; background: var(--paper); overflow: hidden; }

  .brand { position: absolute; left: 34px; top: 45px; height: 94px; display: flex; align-items: center; }
  .brand-dot { width: 64px; height: 64px; border-radius: 50%; background: var(--brand-blue); margin-left: 8px; }
  .brand-rule { width: 1px; height: 94px; background: var(--rule); margin: 0 10px 0 13px; }
  .brand-name { font-family: "Domine", serif; font-weight: 500; color: var(--ink); line-height: 1; }
  .brand-name .primary { display: block; font-size: 35px; letter-spacing: -0.5px; }
  .brand-name .secondary { display: block; font-size: 14px; letter-spacing: 2.6px; margin: 5px 0 0 27px; }

  .contact { position: absolute; left: 657px; top: 52px; height: 80px; border-left: 1px solid var(--rule); padding-left: 12px; font-family: "Roboto Slab", serif; color: var(--ink-soft); }
  .contact-name { font-weight: 300; font-size: 21px; line-height: 1; margin-top: 2px; }
  .contact-line { display: flex; align-items: center; font-size: 15.5px; font-weight: 300; margin-top: 9px; }
  .contact-line svg { width: 14px; height: 14px; margin-right: 10px; flex: none; }

  .footer-address { position: absolute; left: 38px; top: 1160px; font-family: "Roboto Slab", serif; font-size: 17px; font-weight: 300; color: var(--ink-soft); display: flex; align-items: center; }
  .footer-address svg { width: 12px; height: 17px; margin-right: 7px; }
  .footer-bands { position: absolute; left: 0; top: 1155px; width: 931px; height: 45px; }
  .footer-fax { position: absolute; left: 509px; top: 1163px; font-family: "Roboto Slab", serif; font-size: 19px; font-weight: 300; color: #ffffff; display: flex; align-items: center; }
  .footer-fax svg { width: 17px; height: 15px; margin-right: 7px; }
</style>
</head>
<body>
<main class="letterhead">
  <header class="brand">
    <span class="brand-dot"></span>
    <span class="brand-rule"></span>
    <span class="brand-name">
      <span class="primary">KEYSTONE</span>
      <span class="secondary">Endodontics P.C.</span>
    </span>
  </header>

  <section class="contact">
    <p class="contact-name">Bertram L. Oswick, DDS</p>
    <p class="contact-line">
      <svg viewBox="0 0 14 14" aria-hidden="true"><circle cx="7" cy="7" r="6.2" fill="none" stroke="var(--brand-blue)" stroke-width="1.2"/><path d="M5 3.5c-.8.5-1.2 1.5-.8 2.8.5 1.7 1.8 3.4 3.3 4.1.9.4 1.6.2 2-.3l-1.2-1.3-.9.4c-.8-.5-1.4-1.4-1.7-2.3l.7-.6L5.6 3.4z" fill="var(--brand-blue)"/></svg>
      716-392-5061
    </p>
    <p class="contact-line">
      <svg viewBox="0 0 14 14" aria-hidden="true"><rect x="0.5" y="3" width="13" height="8.5" fill="var(--brand-blue)"/><path d="M0.5 3 7 8l6.5-5" fill="none" stroke="#fff" stroke-width="1"/></svg>
      oswickroot@mailhub.net
    </p>
  </section>

  <svg class="footer-bands" viewBox="0 0 931 45" aria-hidden="true">
    <polygon points="0,25 452,25 432,45 0,45" fill="var(--brand-blue)"/>
    <polygon points="502,0 931,0 931,45 441,45" fill="var(--brand-green)"/>
  </svg>

  <p class="footer-address">
    <svg viewBox="0 0 12 17" aria-hidden="true"><path d="M6 0a6 6 0 0 0-6 6c0 4.5 6 11 6 11s6-6.5 6-11a6 6 0 0 0-6-6zm0 8.5A2.5 2.5 0 1 1 6 3.5a2.5 2.5 0 0 1 0 5z" fill="var(--ink-soft)"/></svg>
    2748 Tollard Ave., Suite K, West Tollard, NY 14391
  </p>

  <p class="footer-fax">
    <svg viewBox="0 0 17 15" aria-hidden="true"><rect x="4" y="0.5" width="9" height="4" fill="none" stroke="#fff" stroke-width="1.2"/><rect x="0.5" y="5" width="16" height="7" rx="1.5" fill="#fff"/><rect x="4" y="10" width="9" height="4.5" fill="#fff" stroke="var(--brand-green)" stroke-width="1"/></svg>
    716-392-5087
  </p>
</main>
</body>
</html>
```